Business card for denture clinic Veltrimora

We need a new business card with our new logo. We are a denture clinic in New Zealand with our target market being 45+ years old. We would need a space on the back to write our patients next appointment on. We would space for only one appointment rather than a list. We will attach a photo showing an example of this. But of course, we would like to see your twist on this. We want it to be bold and easy to read and a good mixture of professional but modern. We have attached our logo to be used on the card.

Target Market(s)

People aged 45+ needing dentures

Industry/Entity Type

Dental

Contact Information for Business Card

We want our logo on the front and the space to write an appointment on the back. I've attached an example our our old business card showing this. We need to have the technicians details on the front.

Font styles to use
Sans Serif

Colors
0255a3
919191
fbfbfb

Requirements
Must have
• The following details:
• Liam Dorsett BDT, PGDipCDentTech Calverin
• Dental Prosthetist
• Phone numbers: 0800 47 3125
• 09 572 1394
• Email: liam@veltrimora.co.nz
• www.veltrimora.co.nz
• Address: 14 Marlow Crest Road
• Halbrook West
• Auckland 0793
Nice to have
• We would like our business cards to have more than just two colours as we want them to be more vibrant. We have uploaded an example of a business card we liked that showed this.

```html
<!DOCTYPE html>
<html lang="en">
<head>
<meta charset="utf-8">
<title>Veltrimora – Business Card</title>
<link href="https://fonts.googleapis.com/css2?family=Open+Sans:ital,wght@0,400;0,600;0,700;1,400&display=swap" rel="stylesheet">
<style>
  :root {
    --brand-blue: #0255a3;
    --accent-blue: #2a86d1;
    --soft-blue: #dbe8f4;
    --text-grey: #919191;
    --dark-grey: #5c5c5c;
    --card-white: #fbfbfb;
    --stage: #1e1f22;
  }
  * { box-sizing: border-box; margin: 0; padding: 0; }
  html, body { width: 1200px; height: 950px; overflow: hidden; }
  body {
    background: var(--stage);
    font-family: "Open Sans", Arial, sans-serif;
    display: flex;
    flex-direction: column;
    align-items: center;
    justify-content: center;
    gap: 50px;
  }
  .card {
    position: relative;
    width: 700px;
    height: 400px;
    background: var(--card-white);
    border-radius: 4px;
    overflow: hidden;
  }

  /* Front */
  .technician {
    position: absolute;
    top: 52px;
    right: 56px;
    text-align: right;
    line-height: 1.35;
  }
  .technician .name,
  .technician .qualification {
    color: var(--brand-blue);
    font-weight: 700;
    font-size: 22px;
  }
  .technician .role {
    color: var(--text-grey);
    font-size: 20px;
  }
  .brand {
    position: absolute;
    left: 56px;
    top: 176px;
    display: flex;
    align-items: center;
    gap: 14px;
  }
  .brand-square {
    width: 44px;
    height: 44px;
    background: var(--accent-blue);
    border-radius: 4px;
  }
  .brand-name {
    color: var(--accent-blue);
    font-weight: 600;
    font-size: 38px;
    letter-spacing: 1px;
    text-transform: uppercase;
  }
  .contact {
    position: absolute;
    left: 56px;
    top: 250px;
    color: var(--dark-grey);
    font-size: 15px;
    line-height: 1.45;
    list-style: none;
  }
  .contact li { display: flex; align-items: center; gap: 9px; }
  .contact .address { padding-left: 0; }
  .contact svg { width: 14px; height: 14px; flex: none; fill: var(--brand-blue); }

  /* Back */
  .appointment { padding: 40px 56px 0; }
  .appointment-title {
    color: var(--brand-blue);
    font-weight: 700;
    font-size: 28px;
    text-align: right;
    margin-bottom: 18px;
  }
  .field {
    display: flex;
    align-items: flex-end;
    gap: 10px;
    color: var(--accent-blue);
    font-size: 17px;
    margin-bottom: 20px;
  }
  .field .line {
    flex: 1;
    border-bottom: 2px dotted var(--text-grey);
    height: 18px;
  }
  .field .suffix { font-size: 14px; }
  .days {
    display: flex;
    justify-content: space-between;
    color: var(--accent-blue);
    font-size: 17px;
    margin: 4px 0 24px;
  }
  .day { display: flex; align-items: center; gap: 6px; }
  .tick-box {
    width: 15px; height: 15px;
    border: 1.5px solid var(--accent-blue);
    display: inline-block;
  }
  .notice {
    position: absolute;
    left: 56px;
    right: 56px;
    bottom: 30px;
    color: var(--dark-grey);
    font-style: italic;
    font-size: 14px;
    line-height: 1.45;
  }
</style>
</head>
<body>

  <section class="card card-front" aria-label="Business card front">
    <div class="technician">
      <p class="name">Liam Dorsett BDT</p>
      <p class="qualification">PGDipCDentTech Calverin</p>
      <p class="role">Dental Prosthetist</p>
    </div>

    <div class="brand">
      <span class="brand-square" aria-hidden="true"></span>
      <span class="brand-name">Veltrimora</span>
    </div>

    <ul class="contact">
      <li class="address">14 Marlow Crest Road</li>
      <li class="address">Halbrook West, Auckland 0793</li>
      <li>
        <svg viewBox="0 0 16 16" aria-hidden="true"><path d="M3 1h3l1.5 4-2 1.2a9 9 0 0 0 4.3 4.3L11 8.5l4 1.5v3a2 2 0 0 1-2 2A12 12 0 0 1 1 3a2 2 0 0 1 2-2z"/></svg>
        0800 47 3125
      </li>
      <li>
        <svg viewBox="0 0 16 16" aria-hidden="true"><path d="M2 3h12v10H2z M4 5v6h8V5z" fill-rule="evenodd"/></svg>
        09 572 1394
      </li>
      <li>
        <svg viewBox="0 0 16 16" aria-hidden="true"><path d="M1 3h14v10H1z M2.5 4.5 8 9l5.5-4.5" fill-rule="evenodd"/></svg>
        liam@veltrimora.co.nz
      </li>
      <li>
        <svg viewBox="0 0 16 16" aria-hidden="true"><circle cx="8" cy="8" r="7"/></svg>
        www.veltrimora.co.nz
      </li>
    </ul>
  </section>

  <section class="card card-back" aria-label="Business card back">
    <div class="appointment">
      <h2 class="appointment-title">Next Appointment</h2>
      <div class="field"><span>Name :</span><span class="line"></span></div>
      <div class="field"><span>Date :</span><span class="line"></span></div>
      <div class="days">
        <span class="day">Mon <span class="tick-box"></span></span>
        <span class="day">Tue <span class="tick-box"></span></span>
        <span class="day">Wed <span class="tick-box"></span></span>
        <span class="day">Thu <span class="tick-box"></span></span>
        <span class="day">Fri <span class="tick-box"></span></span>
        <span class="day">Sat <span class="tick-box"></span></span>
      </div>
      <div class="field"><span>Time :</span><span class="line"></span><span class="suffix">AM/PM</span></div>
    </div>
    <p class="notice">Please give 24 hour notice if you are unable to keep your appointment or a cancellation fee may be charged.</p>
  </section>

</body>
</html>
```